Complete redesign of Licensed Medical Cannabis Dispensary website

Redesign website to modernize it and simplify it and add a self service reservation/preorder interactive delivery form. Also integrate current POS system that has current inventory. Here is a website for inspiration that I really like because of it simplicity https://www.leafroute.example and easy ordering option. Attached is our logo.... please design around that and this is our website address www.meadowcrestcourier.example

Font styles to use
Sans Serif

Colors
5c5c5c
cbcbcb
000000
add136

Requirements
Must have
• inventory thats integrated with pos
• online reservation/delivery form
Nice to have
• a website thats modern and simple
• The website designed are the logo that is attached
Should not have
• too much information

```html
<!DOCTYPE html>
<html lang="en">
<head>
<meta charset="utf-8">
<title>Meadowcrest – Medical Delivery</title>
<link rel="stylesheet" href="https://fonts.googleapis.com/css2?family=Open+Sans:ital,wght@0,400;0,600;0,700;0,800;1,400&display=swap">
<style>
:root{
  --green:#9dc437;
  --green-bright:#add136;
  --charcoal:#3f3f3f;
  --grey:#5c5c5c;
  --silver:#bdbdbd;
  --light:#cbcbcb;
  --black:#000;
  --white:#fff;
  --footer-bg:#f1f1f1;
}
*{box-sizing:border-box;margin:0;padding:0}
html,body{width:1200px;height:2913px;overflow:hidden}
body{font-family:"Open Sans",Arial,sans-serif;color:#222;background:var(--white);position:relative}
.abs{position:absolute}
/* header */
.site-header{left:0;top:0;width:1200px;height:134px}
.brand{left:78px;top:44px;display:flex;align-items:center;gap:12px;font-weight:700;font-size:24px;color:var(--green)}
.brand-mark{width:40px;height:40px;border-radius:50%;background:var(--green)}
.header-tools{right:76px;top:38px;display:flex;gap:26px;align-items:center;font-size:12.5px;font-weight:700;color:#222}
.header-tools .cart-total{color:var(--green)}
.main-nav{right:76px;top:89px;display:flex;gap:38px;font-size:12.5px;font-weight:700;color:#222}
/* hero */
.hero{left:0;top:134px;width:1200px;height:449px;
  background:
    radial-gradient(ellipse 260px 300px at 470px 120px,rgba(190,160,140,.75),rgba(190,160,140,0) 70%),
    radial-gradient(ellipse 220px 260px at 120px 140px,rgba(70,120,40,.9),rgba(70,120,40,0) 75%),
    radial-gradient(ellipse 260px 320px at 1050px 220px,rgba(60,110,30,.95),rgba(60,110,30,0) 75%),
    radial-gradient(ellipse 200px 180px at 780px 380px,rgba(80,120,45,.8),rgba(80,120,45,0) 75%),
    radial-gradient(ellipse 180px 160px at 330px 420px,rgba(90,130,50,.8),rgba(90,130,50,0) 75%),
    linear-gradient(180deg,#b9bcb3,#a7ab9e)}
.hero-copy{left:0;top:272px;width:1200px;text-align:center;color:var(--white);text-shadow:0 1px 3px rgba(0,0,0,.35)}
.hero-copy h1{font-size:37px;font-weight:800;line-height:38px;letter-spacing:.5px}
.hero-copy p{font-size:21px;font-weight:700;margin-top:6px}
.hero-actions{left:0;top:406px;width:1200px;display:flex;justify-content:center;gap:30px}
.btn{display:inline-block;font-weight:700;font-size:15px;text-align:center}
.btn-green{background:var(--green-bright);color:var(--white);padding:11px 18px}
.btn-black{background:var(--black);color:var(--white);padding:11px 18px}
.dots{left:0;top:531px;width:1200px;display:flex;justify-content:center;gap:9px}
.dots span{width:11px;height:11px;border-radius:50%;background:#ddd}
.dots span:first-child{background:#333}
/* steps */
.step{top:606px;width:328px;height:235px;color:var(--white);text-align:center;padding-top:30px}
.step h2{font-size:25px;font-weight:700;margin-top:12px}
.step p{font-size:15px;line-height:25px;padding:4px 38px 0}
.step-verify{left:76px;background:var(--green-bright)}
.step-shop{left:435px;background:var(--charcoal)}
.step-med{left:796px;background:var(--silver)}
.divider{left:76px;top:899px;width:1048px;height:2px;background:#ccc}
.tabs{left:0;top:946px;width:1200px;text-align:center;font-size:28px;font-weight:700;color:#333;letter-spacing:1px}
.tabs .active{color:var(--green-bright)}
.tabs .sep{margin:0 28px}
/* products */
.product{width:241px;text-align:center}
.product-photo{width:241px;height:208px;
  background:
    radial-gradient(circle 40px at 30% 35%,rgba(200,190,90,.8),rgba(200,190,90,0)),
    radial-gradient(circle 50px at 70% 60%,rgba(150,160,60,.9),rgba(150,160,60,0)),
    radial-gradient(circle 35px at 55% 20%,rgba(120,80,40,.6),rgba(120,80,40,0)),
    radial-gradient(circle 45px at 20% 80%,rgba(170,170,70,.85),rgba(170,170,70,0)),
    radial-gradient(circle 40px at 85% 15%,rgba(110,130,50,.9),rgba(110,130,50,0)),
    linear-gradient(135deg,#4f5e22,#7d8a35 50%,#3b471a)}
.tone-2{background:
    radial-gradient(circle 50px at 25% 30%,rgba(160,190,70,.9),rgba(160,190,70,0)),
    radial-gradient(circle 45px at 75% 70%,rgba(190,160,80,.8),rgba(190,160,80,0)),
    radial-gradient(circle 40px at 60% 25%,rgba(130,160,60,.9),rgba(130,160,60,0)),
    linear-gradient(135deg,#5e7a2c,#98a94a 50%,#55692a)}
.tone-3{background:
    radial-gradient(circle 45px at 35% 55%,rgba(200,180,80,.85),rgba(200,180,80,0)),
    radial-gradient(circle 55px at 75% 30%,rgba(90,120,40,.9),rgba(90,120,40,0)),
    radial-gradient(circle 40px at 15% 20%,rgba(170,150,60,.8),rgba(170,150,60,0)),
    linear-gradient(135deg,#3f5419,#8a9a3c 55%,#4a5c1f)}
.tone-4{background:
    radial-gradient(circle 50px at 30% 40%,rgba(210,180,90,.85),rgba(210,180,90,0)),
    radial-gradient(circle 45px at 70% 75%,rgba(190,160,70,.8),rgba(190,160,70,0)),
    radial-gradient(circle 40px at 80% 20%,rgba(150,130,60,.8),rgba(150,130,60,0)),
    linear-gradient(135deg,#6d5e2a,#a9964a 50%,#5a5224)}
.tone-5{background:
    radial-gradient(circle 55px at 40% 30%,rgba(140,170,60,.9),rgba(140,170,60,0)),
    radial-gradient(ellipse 90px 40px at 50% 85%,rgba(20,20,20,.85),rgba(20,20,20,0)),
    linear-gradient(160deg,#5d7a2b,#7f9140 55%,#2a2e22)}
.product-name{font-size:15px;margin-top:37px;color:#222}
.product-price{font-size:20px;font-weight:700;color:var(--green-bright);margin-top:4px}
.btn-cart{display:inline-block;margin-top:14px;border:2px solid #333;font-size:13px;font-weight:700;color:var(--green);padding:5px 15px;letter-spacing:1px}
.view-all{left:76px;top:1862px;width:1048px;height:47px;border:2px solid #555;text-align:center;line-height:43px;font-size:13px;font-weight:600;color:#222}
/* testimonial */
.testimonial{left:0;top:1944px;width:1200px;height:384px;color:var(--white);text-align:center;
  background:
    radial-gradient(ellipse 220px 160px at 880px 260px,rgba(110,150,30,.9),rgba(110,150,30,0)),
    radial-gradient(ellipse 260px 180px at 1080px 140px,rgba(190,220,120,.5),rgba(190,220,120,0)),
    radial-gradient(ellipse 280px 200px at 300px 230px,rgba(180,215,100,.5),rgba(180,215,100,0)),
    linear-gradient(180deg,#8dbb2a,#9cc63a)}
.testimonial h3{margin-top:50px;font-size:28px;font-weight:700;letter-spacing:.5px}
.testimonial blockquote{margin:28px auto 0;width:620px;font-size:24px;font-style:italic;line-height:40px}
.avatar{display:block;margin:12px auto 0;width:104px;height:104px;border-radius:50%;
  background:radial-gradient(circle at 50% 45%,#8c6a55,#4a3a30 65%,#2a2a2a);border:3px solid #2c2c2c}
.testimonial cite{display:block;font-style:normal;font-size:16px;font-weight:700;margin-top:14px}
.arrow{top:212px}
/* cta */
.cta{left:76px;top:2356px;width:1048px;height:213px;text-align:center;color:var(--white);
  background:
    radial-gradient(ellipse 200px 120px at 560px 40px,rgba(140,120,50,.6),rgba(140,120,50,0)),
    radial-gradient(ellipse 260px 150px at 900px 150px,rgba(70,100,40,.8),rgba(70,100,40,0)),
    linear-gradient(90deg,#2c2a22,#4a4634 50%,#34421f)}
.cta h3{margin-top:50px;font-size:33px;font-weight:800;letter-spacing:.5px}
.cta .btn-green{margin-top:28px;font-weight:600;font-size:17px;padding:12px 28px}
/* footer */
.site-footer{left:0;top:2610px;width:1200px;height:245px;background:var(--footer-bg)}
.foot-col{top:46px;font-size:12.5px;color:#222}
.foot-col h4{font-size:13px;font-weight:700;margin-bottom:14px}
.foot-col li{list-style:none;margin-bottom:13px}
.newsletter{display:flex;width:212px;height:38px;border:1px solid #333;margin-top:4px;background:#fff}
.newsletter span{flex:1;padding:10px 12px;font-size:12px}
.newsletter b{width:36px;background:#222;display:flex;align-items:center;justify-content:center}
.socials{display:flex;gap:11px;margin-top:4px}
.socials i{width:16px;height:16px;border-radius:50%;background:#222}
.bottom-bar{left:0;top:2855px;width:1200px;height:58px;background:var(--green-bright);color:var(--white);text-align:center;line-height:58px;font-size:12px}
</style>
</head>
<body>
<header class="site-header abs">
  <div class="brand abs"><span class="brand-mark"></span>Meadowcrest</div>
  <div class="header-tools abs">
    <svg width="14" height="14" viewBox="0 0 14 14"><circle cx="6" cy="6" r="4.5" fill="none" stroke="#222" stroke-width="2"/><path d="M9.5 9.5L13 13" stroke="#222" stroke-width="2"/></svg>
    <span><svg width="14" height="12" viewBox="0 0 14 12"><path d="M0 1h3l2 7h7l2-5H4" fill="none" stroke="#222" stroke-width="1.6"/><circle cx="6" cy="10.5" r="1.3" fill="#222"/><circle cx="11" cy="10.5" r="1.3" fill="#222"/></svg> MY CART : <span class="cart-total">$00.00</span></span>
  </div>
  <nav class="main-nav abs"><span>LOGIN/SIGN UP</span><span>CONTACT</span><span>FORUMS</span><span>ORDERS: 555-010-4418</span><span>STORE</span></nav>
</header>

<section class="hero abs" role="img" aria-label="Photo of a grower inspecting cannabis plants in a greenhouse"></section>
<div class="hero-copy abs"><h1>TOP SHELF<br>MEDICAL MARIJUANA DELIVERY</h1><p>We offer only the highest quality flowers, edibles and concentrates.</p></div>
<div class="hero-actions abs"><span class="btn btn-green">SHOP NOW</span><span class="btn btn-black">GET VERIFIED</span></div>
<div class="dots abs"><span></span><span></span><span></span><span></span></div>

<div class="step step-verify abs">
  <svg width="48" height="46" viewBox="0 0 48 46"><rect x="2" y="20" width="10" height="24" fill="#fff"/><path d="M15 20l10-18c4 0 6 3 5 7l-2 9h14c3 0 5 3 4 6l-4 16c-1 3-3 4-6 4H15z" fill="#fff"/></svg>
  <h2>GET VERIFIED</h2><p>It's fast. It's simple. Just fill out our verification form and get approved in minutes.</p>
</div>
<div class="step step-shop abs">
  <svg width="52" height="46" viewBox="0 0 52 46"><path d="M2 4h8l6 26h28l6-20H12" fill="none" stroke="#fff" stroke-width="5"/><rect x="14" y="12" width="33" height="16" fill="#fff"/><circle cx="19" cy="40" r="4.5" fill="#fff"/><circle cx="40" cy="40" r="4.5" fill="#fff"/></svg>
  <h2>SHOP</h2><p>Add the products you want to your shopping cart and check out. No credit card required!</p>
</div>
<div class="step step-med abs">
  <svg width="52" height="46" viewBox="0 0 52 46"><rect x="3" y="10" width="46" height="34" rx="4" fill="none" stroke="#fff" stroke-width="4"/><path d="M18 10V4h16v6" fill="none" stroke="#fff" stroke-width="4"/><path d="M26 17v20M16 27h20" stroke="#fff" stroke-width="6"/></svg>
  <h2>GET MEDICATED</h2><p>Sit back and wait. Our professional staff will deliver your medication right to your front door.</p>
</div>

<div class="divider abs"></div>
<div class="tabs abs"><span class="active">FLOWERS</span><span class="sep">|</span><span>CONCENTRATE</span></div>

<div class="product abs" style="left:76px;top:1033px"><div class="product-photo" role="img" aria-label="Close-up of cannabis flower buds"></div><p class="product-name">Coastal OG (GreenHouse)</p><p class="product-price">$15.00 - $30.00</p><span class="btn-cart">ADD TO CART</span></div>
<div class="product abs" style="left:345px;top:1033px"><div class="product-photo tone-2" role="img" aria-label="Close-up of cannabis flower buds"></div><p class="product-name">Coastal OG (GreenHouse)</p><p class="product-price">$15.00 - $30.00</p><span class="btn-cart">ADD TO CART</span></div>
<div class="product abs" style="left:614px;top:1033px"><div class="product-photo tone-3" role="img" aria-label="Close-up of cannabis flower buds"></div><p class="product-name">Coastal OG (GreenHouse)</p><p class="product-price">$15.00 - $30.00</p><span class="btn-cart">ADD TO CART</span></div>
<div class="product abs" style="left:883px;top:1033px"><div class="product-photo tone-4" role="img" aria-label="Close-up of cannabis flower buds"></div><p class="product-name">Coastal OG (GreenHouse)</p><p class="product-price">$15.00 - $30.00</p><span class="btn-cart">ADD TO CART</span></div>
<div class="product abs" style="left:76px;top:1449px"><div class="product-photo tone-4" role="img" aria-label="Close-up of cannabis flower buds"></div><p class="product-name">Coastal OG (GreenHouse)</p><p class="product-price">$15.00 - $30.00</p><span class="btn-cart">ADD TO CART</span></div>
<div class="product abs" style="left:345px;top:1449px"><div class="product-photo tone-5" role="img" aria-label="Cannabis buds beside a product jar"></div><p class="product-name">Coastal OG (GreenHouse)</p><p class="product-price">$15.00 - $30.00</p><span class="btn-cart">ADD TO CART</span></div>
<div class="product abs" style="left:614px;top:1449px"><div class="product-photo" role="img" aria-label="Close-up of cannabis flower buds"></div><p class="product-name">Coastal OG (GreenHouse)</p><p class="product-price">$15.00 - $30.00</p><span class="btn-cart">ADD TO CART</span></div>
<div class="product abs" style="left:883px;top:1449px"><div class="product-photo tone-2" role="img" aria-label="Close-up of cannabis flower buds"></div><p class="product-name">Coastal OG (GreenHouse)</p><p class="product-price">$15.00 - $30.00</p><span class="btn-cart">ADD TO CART</span></div>

<div class="view-all abs">VIEW ALL PRODUCTS</div>

<section class="testimonial abs" role="img" aria-label="Green-tinted background photo of cannabis buds and lab glassware">
  <h3>WHAT OUR CUSTOMERS SAY ABOUT OUR DISPENSARY...</h3>
  <blockquote>“These guys really know their stuff man. Nothin' but the kind here!”</blockquote>
  <span class="avatar" role="img" aria-label="Customer portrait"></span>
  <cite>MARCO R.</cite>
  <svg class="arrow abs" style="left:74px" width="18" height="28" viewBox="0 0 18 28"><path d="M15 3L4 14l11 11" fill="none" stroke="#fff" stroke-width="4"/></svg>
  <svg class="arrow abs" style="left:1108px" width="18" height="28" viewBox="0 0 18 28"><path d="M3 3l11 11L3 25" fill="none" stroke="#fff" stroke-width="4"/></svg>
</section>

<section class="cta abs" role="img" aria-label="Dark background photo of cannabis flower">
  <h3>STILL NOT A MEMBER OF OUR DISPENSARY?</h3>
  <span class="btn btn-green">GET VERIFIED NOW</span>
</section>

<footer class="site-footer abs">
  <div class="foot-col abs" style="left:76px"><h4>EXPLORE</h4><ul><li>Store</li><li>Cart</li><li>My Account</li><li>New Patient Verification</li><li>Contact Us</li></ul></div>
  <div class="foot-col abs" style="left:336px"><h4>FORUMS</h4><ul><li>Bongs, Bubblers, &amp; Water Pipes</li><li>Concentrates</li><li>Growing</li><li>Vaporizers</li><li>What Are You Smokin'?</li></ul></div>
  <div class="foot-col abs" style="left:645px"><h4>CUSTOMER CARE</h4><ul><li>Order Info</li><li>Shipping / Tracking Info</li><li>Returns Info</li><li>Request Exchange</li><li>Greenline Guarantee</li></ul></div>
  <div class="foot-col abs" style="left:913px"><h4>NEWSLETTER SIGN UP</h4>
    <div class="newsletter"><span>Enter Email</span><b><svg width="14" height="14" viewBox="0 0 14 14"><path d="M1 7L13 1 9 13 7 8z" fill="#fff"/></svg></b></div>
    <h4 style="margin-top:22px">FOLLOW US</h4>
    <div class="socials" aria-label="Social links"><i></i><i></i><i></i><i></i><i></i><i></i><i></i></div>
  </div>
</footer>
<div class="bottom-bar abs">Copyright © 2018. Company Name All Rights Reserved.</div>
</body>
</html>
```